dobbo's business card for earthmoving and tipper hire business.

I have a small earthmoving and tipper truck company. I am aiming for the smaller jobs that the big guys don't want. I am also Doing grass slashing and fire hazard reduction work. I would like to see some earthy colors, greens browns etc. I have a tractor with a front end loader attachment, and a 22 ton tipper. I would like to maybe have a silhouette of a tipper and tractor/slasher/loader setup in centre with my business name over the top and details to one side or something like that

Industry/Entity Type

Business

Contact Information for Business Card

Dobbo's small earthworks and tipper hireToowoombaABN: 47781050480PH 0479126773Email dobbo.3@farrowpost.com

Font styles to use
Sans Serif

Colors
fbee3d
abd036
85cae6
f78f20

Requirements
Nice to have
• Earthy colors . business name in blue

```html
<!DOCTYPE html>
<html lang="en">
<head>
<meta charset="utf-8">
<title>Dobbo's Small Earthworks and Tipper Hire – Business Cards</title>
<link rel="stylesheet" href="https://fonts.googleapis.com/css2?family=Exo+2:wght@400;700;800&display=swap">
<style>
  :root {
    --page-bg: #ececec;
    --card-dark: #2b2b2b;
    --lime: #b5d152;
    --lime-deep: #abd036;
    --orange: #f8a84a;
    --white: #ffffff;
    --ink: #2b2b2b;
    --art-light: #7a7a7a;
    --art-dark: #555555;
  }
  * { box-sizing: border-box; margin: 0; padding: 0; }
  html, body {
    width: 988px;
    height: 1200px;
    overflow: hidden;
    background: var(--page-bg);
    font-family: "Exo 2", Arial, sans-serif;
  }
  .card {
    position: absolute;
    width: 784px;
    height: 455px;
    background: var(--card-dark);
    overflow: hidden;
  }
  .card--lime { left: 94px; top: 102px; }
  .card--orange { left: 96px; top: 626px; }

  .card__background {
    position: absolute;
    inset: 0;
    width: 100%;
    height: 100%;
  }
  .card__title {
    position: absolute;
    left: 0;
    right: 0;
    top: 35px;
    text-align: center;
    color: var(--lime);
    font-weight: 800;
    font-size: 29.5px;
    letter-spacing: 0.6px;
    text-transform: uppercase;
    white-space: nowrap;
  }
  .card__machinery {
    position: absolute;
    left: 70px;
    top: 103px;
    width: 318px;
    height: 166px;
    border-radius: 6px;
    background: linear-gradient(135deg, var(--art-light), var(--art-dark));
  }
  .services {
    position: absolute;
    left: 405px;
    top: 118px;
    list-style: none;
  }
  .services__item {
    display: flex;
    align-items: center;
    height: 34.6px;
    color: var(--white);
    font-weight: 800;
    font-size: 26px;
    letter-spacing: 0.8px;
    white-space: nowrap;
  }
  .services__leaf {
    width: 26px;
    height: 12px;
    margin-right: 6px;
    flex: none;
  }
  .contact {
    position: absolute;
    left: 48px;
    top: 316px;
    list-style: none;
  }
  .contact__item {
    display: flex;
    align-items: center;
    height: 34px;
    color: var(--ink);
    font-size: 22px;
    font-weight: 400;
    letter-spacing: 1.2px;
    white-space: nowrap;
  }
  .contact__icon {
    width: 24px;
    height: 24px;
    margin-right: 8px;
    flex: none;
  }
  .card__abn {
    position: absolute;
    left: 439px;
    top: 384px;
    color: var(--ink);
    font-size: 21px;
    letter-spacing: 1.8px;
    white-space: nowrap;
  }
</style>
</head>
<body>

<svg width="0" height="0" style="position:absolute" aria-hidden="true">
  <defs>
    <symbol id="leaf" viewBox="0 0 26 12">
      <path d="M1 4 C8 -1 20 0 25 8 C17 12 6 11 1 4 Z" fill="#abd036"/>
    </symbol>
    <symbol id="icon-phone" viewBox="0 0 24 24">
      <path d="M7 2 L10 2 L11 7 L8.5 8.5 C9.5 11.5 11.5 14 14.5 15.5 L16 13 L21 14 L21 17 C21 19 19.5 21 17 20.5 C10 19 4.5 13 3.5 6 C3.2 3.8 4.8 2 7 2 Z" fill="none" stroke="#2b2b2b" stroke-width="1.8" stroke-linejoin="round"/>
    </symbol>
    <symbol id="icon-mail" viewBox="0 0 24 24">
      <rect x="2" y="6" width="20" height="13" fill="none" stroke="#2b2b2b" stroke-width="1.8"/>
      <path d="M2 6 L12 14 L22 6 M2 19 L9.5 12 M22 19 L14.5 12" fill="none" stroke="#2b2b2b" stroke-width="1.6"/>
    </symbol>
    <symbol id="icon-pin" viewBox="0 0 24 24">
      <path d="M12 1.5 C7.6 1.5 4.5 4.7 4.5 8.8 C4.5 14 12 22.5 12 22.5 C12 22.5 19.5 14 19.5 8.8 C19.5 4.7 16.4 1.5 12 1.5 Z" fill="#2b2b2b"/>
      <circle cx="12" cy="8.8" r="3" fill="#ececec"/>
    </symbol>
  </defs>
</svg>

<section class="card card--lime">
  <svg class="card__background" viewBox="0 0 708 411" preserveAspectRatio="none" aria-hidden="true">
    <path d="M0 150 C150 270 400 318 708 283 L708 411 L0 411 Z" fill="#b5d152"/>
    <path d="M0 122 C110 228 330 300 708 264 L708 271 C330 310 120 258 0 152 Z" fill="#ffffff"/>
  </svg>
  <h1 class="card__title">Dobbo's small earthworks and tipper hire</h1>
  <div class="card__machinery" role="img" aria-label="White line illustration of a skid steer loader and a tipper truck with raised tray"></div>
  <ul class="services">
    <li class="services__item"><svg class="services__leaf"><use href="#leaf"/></svg>Small earthworks</li>
    <li class="services__item"><svg class="services__leaf"><use href="#leaf"/></svg>Slashing</li>
    <li class="services__item"><svg class="services__leaf"><use href="#leaf"/></svg>Fire hazard reduction</li>
    <li class="services__item"><svg class="services__leaf"><use href="#leaf"/></svg>Rural cleanups</li>
    <li class="services__item"><svg class="services__leaf"><use href="#leaf"/></svg>Tipper</li>
  </ul>
  <ul class="contact">
    <li class="contact__item"><svg class="contact__icon"><use href="#icon-phone"/></svg>0412583906</li>
    <li class="contact__item"><svg class="contact__icon"><use href="#icon-mail"/></svg>dobbo.3@farrowpost.com</li>
    <li class="contact__item"><svg class="contact__icon"><use href="#icon-pin"/></svg>Kelverton</li>
  </ul>
  <p class="card__abn">ABN: 51603928174</p>
</section>

<section class="card card--orange">
  <svg class="card__background" viewBox="0 0 708 411" preserveAspectRatio="none" aria-hidden="true">
    <path d="M0 150 C150 270 400 318 708 283 L708 411 L0 411 Z" fill="#f8a84a"/>
    <path d="M0 122 C110 228 330 300 708 264 L708 271 C330 310 120 258 0 152 Z" fill="#abd036"/>
  </svg>
  <h1 class="card__title">Dobbo's small earthworks and tipper hire</h1>
  <div class="card__machinery" role="img" aria-label="White line illustration of a skid steer loader and a tipper truck with raised tray"></div>
  <ul class="services">
    <li class="services__item"><svg class="services__leaf"><use href="#leaf"/></svg>Small earthworks</li>
    <li class="services__item"><svg class="services__leaf"><use href="#leaf"/></svg>Slashing</li>
    <li class="services__item"><svg class="services__leaf"><use href="#leaf"/></svg>Fire hazard reduction</li>
    <li class="services__item"><svg class="services__leaf"><use href="#leaf"/></svg>Rural cleanups</li>
    <li class="services__item"><svg class="services__leaf"><use href="#leaf"/></svg>Tipper</li>
  </ul>
  <ul class="contact">
    <li class="contact__item"><svg class="contact__icon"><use href="#icon-phone"/></svg>0412583906</li>
    <li class="contact__item"><svg class="contact__icon"><use href="#icon-mail"/></svg>dobbo.3@farrowpost.com</li>
    <li class="contact__item"><svg class="contact__icon"><use href="#icon-pin"/></svg>Kelverton</li>
  </ul>
  <p class="card__abn">ABN: 51603928174</p>
</section>

</body>
</html>
```